Ski Lodge Website update

We need to revamp our website http://www.mlt.org.au to reflect HTML5, larger, beautiful fonts, drop-down menu navigation (no more navigation on left side), addthis twitter/facebook/zorbix+ integration and more, with a twitter feed down the side of the home page (but not on other pages), and great high-res images in a scrolling gallery at the base of the page, with a high-res background.

The current logo is to remain unchanged.

Only images from our own gallery folder can be used - http://www.mlt.org.au/gallery

Requirements
Must have
• MUST be mobile accessible.
• Resulting images and css must be cut and ready for deployment on existing side, to replace existing headers/footers and sidebars.
Nice to have
• Jquery or other js to link offsite (e.g. to zorbix)

```html
<!DOCTYPE html>
<html lang="en">
<head>
<meta charset="utf-8">
<title>Mooroopna Alpine Club – Mt Kestrel</title>
<link href="https://fonts.googleapis.com/css2?family=Open+Sans:wght@400;600;700&display=swap" rel="stylesheet">
<style>
:root{
  --red:#e8383a;
  --red-dark:#b82426;
  --red-text:#e04a45;
  --text:#444;
  --nav-text:#666;
  --footer:#404040;
  --footer-bottom:#363636;
  --footer-rule:#5a5a5a;
  --white:#fff;
}
*{margin:0;padding:0;box-sizing:border-box}
html,body{width:1200px;height:1131px;overflow:hidden;background:var(--white)}
body{position:relative;font-family:"Open Sans",sans-serif;color:var(--text)}
a{color:inherit;text-decoration:none}

.site-header{position:absolute;left:0;top:0;width:1200px;height:77px;background:var(--white)}
.brand{position:absolute;left:176px;top:27px;display:flex;align-items:center;gap:10px}
.brand-mark{width:34px;height:34px;border-radius:50%;background:#d9d9d9}
.brand-name{font-size:15px;color:#777;font-weight:400;letter-spacing:.2px;line-height:1.15}
.main-nav{position:absolute;top:0;left:596px;height:77px;display:flex;font-size:14px;color:var(--nav-text)}
.main-nav a{display:flex;align-items:center;height:77px;padding:0 12px}
.main-nav a.active{background:var(--red);color:var(--white)}

.hero{position:absolute;left:0;top:77px;width:1200px;height:441px;
  background:
   radial-gradient(ellipse 260px 300px at 560px 250px,#b82a2a 0%,#7a1c1c 40%,rgba(60,20,20,0) 100%),
   radial-gradient(ellipse 380px 200px at 200px 380px,#f4f6fa 0%,rgba(240,244,250,0) 100%),
   linear-gradient(180deg,#2f6fe0 0%,#5a94ee 40%,#dfe8f6 80%,#ffffff 100%)}
.hero-title{position:absolute;left:0;top:100px;width:1200px;text-align:center;font-size:41px;line-height:50px;color:var(--white);text-shadow:0 2px 4px rgba(0,0,0,.5);font-weight:400}
.slide-arrow{position:absolute;top:195px;width:43px;height:51px;background:var(--red);border-bottom:3px solid var(--red-dark)}
.slide-arrow.prev{left:0}
.slide-arrow.next{right:0}
.slide-arrow svg{position:absolute;left:11px;top:14px}
.hero-actions{position:absolute;top:356px;left:387px;display:flex;gap:18px}
.btn{display:flex;align-items:center;justify-content:center;background:var(--red);color:var(--white);border-bottom:4px solid var(--red-dark);border-radius:3px;text-shadow:0 1px 2px rgba(0,0,0,.35)}
.btn-hero{width:205px;height:60px;font-size:27px}

.intro{position:absolute;left:173px;top:538px;width:858px;font-size:12.5px;line-height:18px}
.intro h1{font-size:31px;font-weight:600;color:var(--red-text);line-height:44px;margin-bottom:8px}
.features li{list-style:none;color:var(--red-text)}
.booking-phone span{color:var(--red-text);margin-right:32px}
.specials{position:absolute;left:173px;top:797px;width:858px;text-align:right;font-size:12.5px;line-height:18px;color:var(--red-text)}
.specials a{text-decoration:underline}
.btn-cta{position:absolute;left:174px;top:842px;width:153px;height:56px;font-size:21px}

.site-footer{position:absolute;left:0;top:923px;width:1200px;height:165px;background:var(--footer);color:var(--white)}
.footer-col{position:absolute;top:12px}
.footer-col h3{font-size:17px;font-weight:700;line-height:20px;margin-bottom:5px}
.footer-col ul{list-style:none;font-size:10.5px;line-height:20.5px}
.footer-col li::before{content:"›";margin-right:8px;font-size:13px}
.rule{position:absolute;top:30px;width:1px;height:122px;background:var(--footer-rule)}
.blog-thumb{position:absolute;left:0;top:30px;width:65px;height:65px;border:2px solid var(--white);border-radius:4px;background:var(--red)}
.blog-thumb svg{position:absolute;left:17px;top:18px}
.blog-text{position:absolute;left:74px;top:36px;width:220px;font-size:11px;line-height:17px}
.blog-meta{color:var(--red-text);margin-top:9px}
.contact-info{font-size:11px;line-height:20px;width:260px}
.contact-info .label{color:var(--red-text)}

.footer-bottom{position:absolute;left:0;top:1088px;width:1200px;height:43px;background:var(--footer-bottom);color:var(--white);font-size:10.5px}
.copyright{position:absolute;left:177px;top:14px}
.social{position:absolute;left:892px;top:10px;display:flex;gap:21px}
.social span{display:block;width:18px;height:18px;border-radius:50%;background:var(--red)}
</style>
</head>
<body>

<header class="site-header">
  <div class="brand">
    <span class="brand-mark"></span>
    <span class="brand-name">MOOROOPNA ALPINE CLUB<br>MT.KESTREL</span>
  </div>
  <nav class="main-nav">
    <a class="active" href="#">Home</a>
    <a href="#">Rates</a>
    <a href="#">Location</a>
    <a href="#">Facillties</a>
    <a href="#">Member</a>
    <a href="#">Contact Us</a>
  </nav>
</header>

<section class="hero" role="img" aria-label="Blurred photo of a skier in a red suit racing downhill under a blue sky">
  <h2 class="hero-title">A Great alpine holiday experience<br>in one of Kestrel's<br>best ski lodger</h2>
  <a class="slide-arrow prev" href="#" aria-label="Previous slide">
    <svg width="22" height="22" viewBox="0 0 22 22" fill="none" stroke="#fff" stroke-width="2.5"><path d="M11 3 3 11l8 8M19 3l-8 8 8 8"/></svg>
  </a>
  <a class="slide-arrow next" href="#" aria-label="Next slide">
    <svg width="22" height="22" viewBox="0 0 22 22" fill="none" stroke="#fff" stroke-width="2.5"><path d="M3 3l8 8-8 8M11 3l8 8-8 8"/></svg>
  </a>
  <div class="hero-actions">
    <a class="btn btn-hero" href="#">SignUp</a>
    <a class="btn btn-hero" href="#">Booking</a>
  </div>
</section>

<main class="intro">
  <h1>Mt Kestrel Accommodation</h1>
  <ul class="features">
    <li>Spectacular alpine views</li>
    <li>Modern, well appointed accommodation</li>
    <li>Close to M t Kestrel facilities &amp; ski slopes</li>
    <li>Ideal family accommodation</li>
  </ul>
  <p>The ideal Mt Kestrel accommodation for your snow holiday. The Mooroopna Alpine Ski Lodge is multi-level, modern, comfortable and well appointed.</p>
  <p>Mt Kestrel Village facilities, transport, ski lifts and shops are all nearby.</p>
  <p>The spacious lounge and dining areas have breathtaking views of the alps surrounding Mt Kestrel. There's a games room, new modern kitchen with barbecue,</p>
  <p>an open fire, a large balcony, guest laundry, drying room and ski room.</p>
  <p class="booking-phone"><span>Booking phone:</span>0400 123 456</p>
</main>

<div class="specials">
  <a href="#">Room rate special from $208 per night!</a><br>
  <a href="#">Adults stay at kids prices when full room booked mid-week for 3 or more nights!</a>
</div>
<a class="btn btn-cta" href="#">Click here!</a>

<footer class="site-footer">
  <div class="footer-col" style="left:171px">
    <h3>Menu</h3>
    <ul><li>Home</li><li>Rates</li><li>Location</li><li>Facillties</li><li>Member Login</li></ul>
  </div>
  <span class="rule" style="left:315px"></span>
  <div class="footer-col" style="left:331px">
    <h3>Menu</h3>
    <ul><li>How to Join</li><li>Luggage</li><li>Transport</li><li>Partner Offers</li><li>Contact Us</li></ul>
  </div>
  <span class="rule" style="left:434px"></span>
  <div class="footer-col" style="left:456px">
    <h3>Blog</h3>
    <div class="blog-thumb">
      <svg width="28" height="24" viewBox="0 0 28 24" fill="none" stroke="#fff" stroke-width="2"><rect x="1" y="1" width="26" height="22" rx="2"/><circle cx="9" cy="8" r="2.5" fill="#fff"/><path d="M3 20l7-7 4 4 5-6 6 9z" fill="#fff"/></svg>
    </div>
    <div class="blog-text">
      <p>Lorem ipsum dolor sit amet, consectetur adipiscing elit</p>
      <p class="blog-meta">Lorem ipsum &nbsp;|&nbsp; 26 May, 2013</p>
    </div>
  </div>
  <span class="rule" style="left:755px"></span>
  <div class="footer-col" style="left:771px">
    <h3>Contact Information</h3>
    <div class="contact-info">
      <p>Mooroopna Alpine Club @ Mount KestrelLorem</p>
      <p><span class="label">Phone:</span> 03 5550 1234 &nbsp;| &nbsp;<span class="label">FAX:</span> 03 5550 5678 <span class="label">(winter only)</span></p>
      <p>Mount Kestrel, Victoria 3999, Australia</p>
    </div>
  </div>
</footer>

<div class="footer-bottom">
  <p class="copyright">2013 &nbsp;all rights reserved</p>
  <div class="social">
    <span aria-label="Social link 1"></span>
    <span aria-label="Social link 2"></span>
    <span aria-label="Social link 3"></span>
    <span aria-label="News feed"></span>
  </div>
</div>

</body>
</html>
```